Audio/ Video Packaging Design for a Technology company.

We need a packaging design for a bag that is 7" wide and 10" high. The design will be for a new line of audio/video products. We would like to see designs that represent a superior quality product that provides a pure connection. We want the equivalent of a nice retail bag that you would find in a store like Tallow Mart. It should be a maximum of three colors. We really want something sharp, professional and eye catching, not whimsical or cartoonish. I've included a couple of examples below. I don't really like the designs of the bags, but I want you to see examples of what I'm looking for.

The company logo, which is uploaded, should be on the design. The words "audio and video products" should be either underneath the logo or to the side. Also, somewhere on the bag, we would like the words "Clean Signal, Every Time"

The winner of this contest will likely get the opportunity for additional work as we have more products ready to launch.

Target Market(s)

resellers, consumers - men 25-60

Industry/Entity Type

It Company

Requirements
Must have
• It should be a maximum of three colors. We really want something sharp, professional and eye catching, not whimsical or cartoonish
Nice to have
• Eye-catching design. Utilize the entire bag but don't make it too busy.
Should not have
• Whimsical, cartoonish

```html
<!DOCTYPE html>
<html lang="en">
<head>
<meta charset="utf-8">
<title>Veridon Bag Packaging</title>
<link rel="stylesheet" href="https://fonts.googleapis.com/css2?family=Montserrat:wght@400;500;600;700&display=swap">
<style>
  :root {
    --stage: #7f8082;
    --bag-white: #ffffff;
    --bag-dark: #3a3b3d;
    --sky-blue: #5ec3f0;
    --royal-blue: #3273c4;
    --text-blue: #4fb8ee;
    --ink: #2f3033;
    --muted: #9a9b9d;
  }
  html, body {
    margin: 0;
    padding: 0;
    width: 1200px;
    height: 960px;
    overflow: hidden;
    background: var(--stage);
    font-family: "Montserrat", sans-serif;
  }
  .stage {
    position: relative;
    width: 1200px;
    height: 960px;
  }
  .bag {
    position: absolute;
    top: 206px;
    width: 482px;
    height: 713px;
  }
  .bag--brand { left: 61px; }
  .bag--cable { left: 654px; }
  .bag svg { display: block; }
  .brand-name { font-weight: 500; letter-spacing: 2px; }
  .brand-line { font-weight: 500; letter-spacing: 3px; }
  .tagline { font-weight: 500; }
  .origin { font-weight: 600; letter-spacing: 1px; }
  .cable-word { font-weight: 700; }
  .power-word { font-weight: 600; }
  .voltage { font-weight: 500; }
</style>
</head>
<body>
<main class="stage">

  <!-- Front face: brand bag -->
  <div class="bag bag--brand">
    <svg width="482" height="713" viewBox="0 0 482 713">
      <defs>
        <clipPath id="bag-shape-a"><rect width="482" height="713" rx="30"/></clipPath>
        <linearGradient id="window-a" x1="0" y1="0" x2="1" y2="1">
          <stop offset="0" stop-color="#cfd0d2"/>
          <stop offset="0.45" stop-color="#f2f2f3"/>
          <stop offset="1" stop-color="#c4c5c7"/>
        </linearGradient>
      </defs>
      <g clip-path="url(#bag-shape-a)">
        <rect width="482" height="713" fill="var(--bag-white)"/>
        <line x1="8" y1="94" x2="474" y2="94" stroke="#e2e2e2" stroke-dasharray="5 4"/>
        <rect x="44" y="106" width="392" height="520" rx="30" fill="url(#window-a)" role="img" aria-label="Clear window showing the packed product"/>
        <polygon points="0,282 291,482 482,214 482,713 0,713" fill="var(--sky-blue)"/>
        <polygon points="0,298 293,506 482,232 482,713 0,713" fill="var(--bag-white)"/>
        <polygon points="0,310 298,532 482,246 482,713 0,713" fill="var(--bag-dark)"/>
        <g class="brand-block">
          <rect x="158" y="558" width="30" height="30" fill="var(--bag-white)"/>
          <text class="brand-name" x="200" y="588" font-size="42" fill="var(--bag-white)">VERIDON</text>
          <text class="brand-line" x="299" y="627" font-size="16.5" fill="var(--text-blue)" text-anchor="middle">audio and video products</text>
        </g>
        <text class="tagline" x="299" y="677" font-size="22" fill="var(--bag-white)" text-anchor="middle">“Clean Signal, Every Time”</text>
        <text class="origin" transform="translate(26,672) rotate(-90)" font-size="8" fill="var(--muted)">MADE IN CHINA</text>
      </g>
    </svg>
  </div>

  <!-- Back face: cable bag -->
  <div class="bag bag--cable">
    <svg width="482" height="713" viewBox="0 0 482 713">
      <defs>
        <clipPath id="bag-shape-b"><rect width="482" height="713" rx="30"/></clipPath>
        <linearGradient id="window-b" x1="0" y1="0" x2="1" y2="1">
          <stop offset="0" stop-color="#c9cacc"/>
          <stop offset="0.5" stop-color="#f4f4f5"/>
          <stop offset="1" stop-color="#cbcccd"/>
        </linearGradient>
      </defs>
      <g clip-path="url(#bag-shape-b)">
        <rect width="482" height="713" fill="var(--bag-white)"/>
        <line x1="8" y1="94" x2="474" y2="94" stroke="#e2e2e2" stroke-dasharray="5 4"/>
        <rect x="53" y="113" width="373" height="510" rx="30" fill="url(#window-b)" role="img" aria-label="Clear window showing the packed cable"/>
        <g class="brand-block">
          <rect x="104" y="135" width="26" height="26" fill="var(--ink)"/>
          <text class="brand-name" x="140" y="161" font-size="38" fill="var(--ink)">VERIDON</text>
          <rect x="94" y="185" width="304" height="25" rx="4" fill="var(--ink)"/>
          <text class="brand-line" x="246" y="203" font-size="16" fill="var(--text-blue)" text-anchor="middle">audio and video products</text>
        </g>
        <polygon points="0,306 290,502 482,234 482,713 0,713" fill="var(--royal-blue)"/>
        <polygon points="0,322 292,524 482,252 482,713 0,713" fill="var(--bag-white)"/>
        <polygon points="0,334 296,548 482,266 482,713 0,713" fill="var(--bag-dark)"/>
        <text class="origin" transform="translate(37,534) rotate(-90)" font-size="8" fill="var(--muted)">MADE IN CHINA</text>
        <rect x="26" y="542" width="26" height="104" fill="var(--text-blue)"/>
        <text class="power-word" transform="translate(47,643) rotate(-90)" font-size="20" fill="var(--bag-dark)">POWER</text>
        <text class="voltage" transform="translate(75,643) rotate(-90)" font-size="18" fill="var(--text-blue)">110V ~300V</text>
        <text class="cable-word" x="90" y="643" font-size="66" fill="var(--text-blue)">CABLE</text>
        <line x1="26" y1="649" x2="330" y2="649" stroke="var(--text-blue)" stroke-width="2"/>
        <text class="tagline" x="210" y="674" font-size="20" fill="var(--bag-white)" text-anchor="middle">“Clean Signal, Every Time”</text>
      </g>
    </svg>
  </div>

</main>
</body>
</html>
```